Radon Reduction & Mold Removal Website

I need you to set up a WordPress account for me and design a full width, professional-looking, mobile-responsive website for my business. We offer radon reduction and mold removal (two household environmental issues).
We have merged 2 companies and need a single website to promote both services (radon and mold). Here are the current websites from the 2 businesses that have merged:
RADON
http://plinth-airworks.com/
MOLD
http://quellbright-spores.net/
Once complete, I will need the login to the WordPress account so I have access to the site to make changes, additions, and modifications.
Target Market(s)
Home Owners
Industry/Entity Type
Home And Garden
Look and feel
Each slider illustrates characteristics of the customer's brand and the style your logo design should communicate.

```html
<!DOCTYPE html>
<html lang="en">
<head>
<meta charset="utf-8">
<title>Kestrel Environmental – Mold Removal &amp; Radon Reduction</title>
<link rel="stylesheet" href="https://fonts.googleapis.com/css2?family=Roboto+Condensed:wght@300;400;700&family=Roboto:wght@300;400;700&display=swap">
<style>
  :root {
    --header-bg: #1c1c1c;
    --brand-yellow: #f2e21a;
    --nav-active: #c9d61c;
    --nav-text: #e6e6e6;
    --page-bg: #ffffff;
    --heading: #3d3d3d;
    --body-text: #8a8a8a;
    --accent-green: #3c9a1e;
    --service-green: #58b548;
    --divider: #e2e2e2;
  }
  * { box-sizing: border-box; margin: 0; padding: 0; }
  html, body { width: 1200px; height: 725px; overflow: hidden; background: var(--page-bg); }
  body { font-family: "Roboto", Arial, sans-serif; position: relative; }

  .site-header {
    position: absolute; left: 0; top: 0; width: 1200px; height: 102px;
    background: var(--header-bg);
  }
  .brand {
    position: absolute; left: 182px; top: 12px; display: flex; align-items: center; gap: 10px;
  }
  .brand-square { width: 18px; height: 18px; background: var(--brand-yellow); }
  .brand-name {
    font-family: "Roboto Condensed", Arial, sans-serif; font-weight: 700;
    font-size: 24px; line-height: 26px; color: var(--brand-yellow); letter-spacing: 1px;
    width: 160px;
  }
  .phone {
    position: absolute; left: 893px; top: 12px; display: flex; align-items: center; gap: 6px;
    font-family: "Roboto Condensed", Arial, sans-serif; font-size: 14px; color: var(--brand-yellow);
  }
  .main-nav { position: absolute; top: 62px; left: 0; width: 1200px; }
  .main-nav a {
    position: absolute; font-family: "Roboto Condensed", Arial, sans-serif; font-weight: 300;
    font-size: 15px; color: var(--nav-text); text-decoration: none; white-space: nowrap;
  }
  .main-nav a.is-current { color: var(--nav-active); }

  .hero {
    position: absolute; left: 0; top: 102px; width: 1200px; height: 362px;
    background: linear-gradient(180deg, #8fb2d6 0%, #b9cfe2 30%, #a8927a 55%, #8a6e52 75%, #5f6a3c 92%, #3f5326 100%);
  }
  .hero-title {
    position: absolute; left: 0; width: 1222px; top: 120px; text-align: center;
    font-family: "Roboto Condensed", Arial, sans-serif; font-weight: 700; font-size: 27px;
    color: #ffffff; text-shadow: 0 1px 4px rgba(0,0,0,0.7);
  }

  .welcome { position: absolute; left: 0; top: 464px; width: 1200px; height: 175px; text-align: center; }
  .welcome h1 {
    margin-top: 26px; font-weight: 400; font-size: 22px; color: var(--heading);
  }
  .welcome h1 strong { color: var(--accent-green); font-weight: 700; }
  .welcome p {
    width: 836px; margin: 8px auto 0; font-size: 11px; line-height: 17px; color: var(--body-text);
  }
  .welcome .more-link {
    display: inline-block; margin-top: 10px; font-size: 12px; font-weight: 700;
    color: var(--accent-green); text-decoration: none;
  }
  .section-shadow {
    position: absolute; left: 0; top: 636px; width: 1200px; height: 8px;
    background: linear-gradient(180deg, rgba(0,0,0,0.08), rgba(0,0,0,0));
  }

  .services { position: absolute; left: 0; top: 650px; width: 1200px; height: 75px; }
  .service { position: absolute; top: 0; text-align: center; }
  .service h2 {
    font-weight: 400; font-size: 16px; color: var(--service-green); white-space: nowrap;
  }
  .service-photo { position: absolute; top: 28px; height: 60px; }
  .service-divider { position: absolute; top: 20px; width: 1px; height: 60px; background: var(--divider); }
</style>
</head>
<body>
  <header class="site-header">
    <div class="brand">
      <span class="brand-square"></span>
      <span class="brand-name">KESTREL ENVIRONMENTAL</span>
    </div>
    <div class="phone">
      <svg width="14" height="12" viewBox="0 0 14 12" aria-hidden="true">
        <path d="M1 4 Q7 -1 13 4 L11 6 L9 4.5 L5 4.5 L3 6 Z" fill="#f2e21a"/>
        <rect x="3" y="6" width="8" height="5" rx="1" fill="#f2e21a"/>
      </svg>
      <span>(888) 555-0142</span>
    </div>
    <nav class="main-nav">
      <a class="is-current" href="#" style="left:477px">HOME</a>
      <a href="#" style="left:552px">ABOUT US</a>
      <a href="#" style="left:657px">OUR SERVICES</a>
      <a href="#" style="left:794px">OUR PRODUCT</a>
      <a href="#" style="left:931px">GET A GOUTE</a>
    </nav>
  </header>

  <section class="hero" role="img" aria-label="Large two-storey brick and stucco family house with a stone chimney under a blue sky">
    <h2 class="hero-title">MOLD REMOVAL &amp; RADON REDUCTION</h2>
  </section>

  <section class="welcome">
    <h1>Welcome to <strong>KESTREL</strong></h1>
    <p>Lorem ipsum dolor sit amet, consectetur adipiscing elit, sed do eiusmod tempor incididunt ut labore et dolore magna aliqua. Ut enim ad minim veniam, quis nostrud exercitation ullamco laboris nisi ut aliquip ex ea commodo consequat. Lorem ipsum dolor sit amet, consectetur adipiscing elit, sed do eiusmod tempor incididunt ut labore et dolore magna aliqua. Ut enim ad minim veniam, quis nostrud exercitation ullamco laboris nisi ut aliquip ex ea commodo consequat.</p>
    <a class="more-link" href="#">Our More Services....</a>
  </section>
  <div class="section-shadow"></div>

  <section class="services">
    <div class="service" style="left:266px;width:160px"><h2>Residential Services</h2></div>
    <div class="service-photo" role="img" aria-label="Worker on a ladder beside a house wall" style="left:247px;width:203px;background:linear-gradient(135deg,#9c8670,#c9c2b4 60%,#7d8aa0)"></div>
    <div class="service-divider" style="left:477px"></div>

    <div class="service" style="left:518px;width:160px"><h2>Commercial Services</h2></div>
    <div class="service-photo" role="img" aria-label="Radon mitigation pipe mounted on a building exterior" style="left:506px;width:180px;background:linear-gradient(135deg,#b7ab92,#d8d0bc 55%,#8e9a78)"></div>
    <div class="service-divider" style="left:723px"></div>

    <div class="service" style="left:764px;width:160px"><h2>Real Estate Services</h2></div>
    <div class="service-photo" role="img" aria-label="Real estate agent showing a home" style="left:766px;width:174px;background:linear-gradient(135deg,#c79a6e,#e4ddd2 55%,#8aa3c0)"></div>
  </section>
</body>
</html>
```